Marlowe Group needs a business card

I would like the card to be simple but modern and elegant.
I like black and white.
or black and gold.
we are a private finance lender and also are involved in property and property developments.

please look at the business card photos i provided i would like M.G only one one side and all the other details on the other side use fonts that tie in with my theme.

Industry/Entity Type

Finance

Contact Information for Business Card

Marlowe Group (M.G) Daniel Marlowe M: 0413586207 E: danmarl@inboxmail.test

Font styles to use
Other font styles liked:
• Use fonts that would reflect our business

Colors
000000
ffffff

Requirements
Must have
• one side of details
• other side has either M.G or Marlowe Group like in the photos provided

```html
<!DOCTYPE html>
<html lang="en">
<head>
<meta charset="utf-8">
<title>Marlowe Group — Business Card</title>
<link href="https://fonts.googleapis.com/css2?family=Cinzel:wght@400;700&family=Lato:wght@400&display=swap" rel="stylesheet">
<style>
  :root {
    --page-bg: #e9e6e3;
    --frost-top: #f7f5f3;
    --frost-bottom: #e4e1de;
    --band-dark: #15161a;
    --band-mid: #2a2b30;
    --ink: #111111;
    --ink-faint: rgba(17, 17, 17, 0.35);
    --paper: #ffffff;
    --rule: rgba(255, 255, 255, 0.45);
  }
  * { box-sizing: border-box; margin: 0; padding: 0; }
  html, body {
    width: 1200px;
    height: 900px;
    overflow: hidden;
    background: var(--page-bg);
  }
  .canvas {
    position: relative;
    width: 1200px;
    height: 900px;
  }
  .card {
    position: absolute;
    width: 555px;
    height: 345px;
    border-radius: 30px;
    overflow: hidden;
    background: linear-gradient(180deg, var(--frost-top), var(--frost-bottom));
    box-shadow: 0 10px 30px rgba(0, 0, 0, 0.12);
  }
  .card--front { left: 238px; top: 60px; }
  .card--back  { left: 459px; top: 520px; }

  .card__brand {
    position: absolute;
    left: 0; right: 0; top: 0;
    height: 195px;
    display: flex;
    flex-direction: column;
    align-items: center;
  }
  .brand-square {
    margin-top: 32px;
    width: 112px;
    height: 112px;
    border: 3px solid var(--ink);
  }
  .brand-name {
    margin-top: 10px;
    font-family: "Cinzel", serif;
    font-weight: 400;
    font-size: 19px;
    letter-spacing: 0.5px;
    color: var(--ink);
  }
  .card--back .card__brand { transform: scaleX(-1); }
  .card--back .brand-square { border-color: var(--ink-faint); border-width: 2px; }
  .card--back .brand-name { color: var(--ink-faint); }

  .card__band {
    position: absolute;
    left: 0; right: 0; bottom: 0;
    height: 150px;
    background: linear-gradient(180deg, var(--band-dark), var(--band-mid) 50%, var(--band-dark));
  }
  .card--back .card__band { height: 150px; }

  .details {
    display: flex;
    flex-direction: column;
    align-items: center;
    color: var(--paper);
    padding-top: 38px;
  }
  .details__name {
    font-family: "Cinzel", serif;
    font-weight: 700;
    font-size: 20px;
    letter-spacing: 0.6px;
  }
  .details__rule {
    width: 150px;
    height: 1px;
    margin: 12px 0 14px;
    background: var(--rule);
  }
  .details__contact {
    font-family: "Lato", sans-serif;
    font-size: 15px;
    letter-spacing: 0.2px;
  }
  .monogram-field {
    position: absolute;
    inset: 0;
    background:
      repeating-linear-gradient(90deg, rgba(255,255,255,0.04) 0 48px, transparent 48px 59px),
      linear-gradient(180deg, var(--band-dark), var(--band-mid) 50%, var(--band-dark));
  }
</style>
</head>
<body>
<main class="canvas">

  <section class="card card--front" aria-label="Business card front">
    <div class="card__brand">
      <div class="brand-square"></div>
      <p class="brand-name">Marlowe Group</p>
    </div>
    <div class="card__band">
      <div class="details">
        <p class="details__name">DANIEL MARLOWE</p>
        <div class="details__rule"></div>
        <p class="details__contact">M: 0413586207 &nbsp;| &nbsp;E: danmarl@inboxmail.test</p>
      </div>
    </div>
  </section>

  <section class="card card--back" aria-label="Business card back">
    <div class="card__brand">
      <div class="brand-square"></div>
      <p class="brand-name">Marlowe Group</p>
    </div>
    <div class="card__band">
      <div class="monogram-field" role="img" aria-label="Repeating tone-on-tone monogram pattern on black"></div>
    </div>
  </section>

</main>
</body>
</html>
```